Marwick Family Chiropractic Stationary

The letterhead and business card must have our logo.
We would like to see the logo used in different ways ( It can be expanded upon in the stationary.)
Please use the the same or similar colors.
Must be eye catching and memorable.
Must be easy to read

Reason: The doctor has been too busy to make any final decisions. He would like to give himself a little more time.

Target Market(s)

Chiropractic Healthcare

Industry/Entity Type

Business

Requirements
Must have
• Dr. Leonard Marwick D.C.
Chiropractor

860-555-0183

417 Birchfield Road, 2nd Floor
Elmcrest, ME 06091

drmarwick@marwickspine.example
www.marwickspine.example
www.social.example/MarwickFamilySpine
Should not have
• should not be difficult to read

```html
<!DOCTYPE html>
<html lang="en">
<head>
<meta charset="utf-8">
<title>Marwick Family Chiropractic – Business Card</title>
<link rel="stylesheet" href="https://fonts.googleapis.com/css2?family=League+Spartan:wght@500;600;700&display=swap">
<style>
  :root {
    --green: #2f9148;
    --leaf-green: #4caf50;
    --ink: #231f20;
    --paper: #ffffff;
  }
  * { margin: 0; padding: 0; box-sizing: border-box; }
  html, body {
    width: 1200px;
    height: 667px;
    overflow: hidden;
    background: var(--paper);
  }
  .card {
    position: relative;
    width: 1200px;
    height: 667px;
    background: var(--paper);
    font-family: "League Spartan", "Century Gothic", sans-serif;
    color: var(--ink);
  }
  .identity {
    position: absolute;
    left: 565px;
    top: 58px;
    white-space: nowrap;
  }
  .doctor-name {
    font-size: 56px;
    font-weight: 600;
    line-height: 1;
    letter-spacing: 0.2px;
  }
  .doctor-name .accent { color: var(--green); }
  .profession {
    margin-top: 10px;
    font-size: 25px;
    font-weight: 500;
    letter-spacing: 42px;
    line-height: 1;
  }
  .contact {
    position: absolute;
    left: 565px;
    top: 400px;
    list-style: none;
    white-space: nowrap;
    font-size: 31px;
    line-height: 35.5px;
    font-weight: 700;
  }
  .contact .accent { color: var(--green); }
  .contact .web { font-size: 30px; font-weight: 600; }
  .brand {
    position: absolute;
    left: 11px;
    top: 276px;
    width: 362px;
    height: 391px;
    display: flex;
    flex-direction: column;
    align-items: center;
    justify-content: center;
    gap: 22px;
  }
  .brand-mark {
    width: 96px;
    height: 96px;
    border-radius: 50%;
    background: var(--leaf-green);
  }
  .brand-name {
    font-size: 30px;
    font-weight: 600;
    line-height: 1.15;
    text-align: center;
    color: var(--green);
  }
</style>
</head>
<body>
  <main class="card">
    <div class="brand">
      <div class="brand-mark"></div>
      <p class="brand-name">Marwick Family<br>Chiropractic</p>
    </div>

    <header class="identity">
      <h1 class="doctor-name"><span class="accent">Dr. Leonard</span> Marwick D.C.</h1>
      <p class="profession">Chiropractor</p>
    </header>

    <ul class="contact">
      <li class="accent">860-555-0183</li>
      <li><span class="accent">417</span> Birchfield Road, 2nd Floor</li>
      <li>Elmcrest, ME <span class="accent">06091</span></li>
      <li class="web">drmarwick@marwickspine.example</li>
      <li class="web">www.marwickspine.example</li>
      <li class="web">www.social.example/MarwickFamilySpine</li>
    </ul>
  </main>
</body>
</html>
```